Business Card Design - Amberfield Court

We are looking at a new design for our business cards that has a modern and professional look. We run a residential aged care facility focussing on the care of residents. The cards will be used for potential clients, consultants and business opportunities in this sector. Blue and white is our main colours and would to see these colours incorporated in the design.
Industry/Entity Type
Business
Contact Information for Business Card
Amberfield Court, Darren Walsh, dwalsh@amberfieldcourt.com.au, Finance Manager, 0472 639 208, BCom, 37 Marrabel Crescent, Brindle Vale, Qld 4093.
Look and feel
Each slider illustrates characteristics of the customer's brand and the style your logo design should communicate.

```html
<!DOCTYPE html>
<html lang="en">
<head>
<meta charset="utf-8">
<title>Amberfield Court – Business Card</title>
<link rel="stylesheet" href="https://fonts.googleapis.com/css2?family=PT+Sans:wght@400;700&display=swap">
<style>
  :root {
    --page-bg: #2b2624;
    --card-bg: #0f0f11;
    --brand-blue: #4d7a96;
    --brand-sand: #b5a59b;
    --text-light: #f2f2f2;
    --text-muted: #d9d9d9;
  }
  * { margin: 0; padding: 0; box-sizing: border-box; }
  html, body {
    width: 1200px; height: 844px; overflow: hidden;
    background: var(--page-bg);
    font-family: "PT Sans", Arial, sans-serif;
  }
  .sheet {
    position: relative; width: 1200px; height: 844px;
    display: flex; align-items: center; justify-content: center; gap: 40px;
  }
  .card {
    position: relative; width: 540px; height: 309px; overflow: hidden;
    background: var(--card-bg);
    box-shadow: 0 10px 30px rgba(0,0,0,.45);
  }
  .brand {
    position: absolute; display: flex; flex-direction: column; align-items: center;
  }
  .brand__row { display: flex; align-items: center; gap: 10px; }
  .brand__dot {
    width: 22px; height: 22px; border-radius: 50%; background: var(--brand-blue);
  }
  .brand__name {
    color: var(--brand-blue); font-weight: 700; font-size: 26px; line-height: 30px;
    letter-spacing: 1px; text-transform: uppercase; white-space: nowrap;
  }
  .brand__tagline {
    margin-top: 8px; color: var(--brand-sand); font-size: 14px; line-height: 18px; white-space: nowrap;
  }
  .card--front .brand { right: 36px; top: 56px; }
  .card--back .brand { left: 50%; top: 50%; transform: translate(-50%, -50%); }
  .card--back .brand__name { font-size: 30px; line-height: 34px; }
  .card--back .brand__tagline { font-size: 16px; line-height: 20px; }

  .contact {
    position: absolute; right: 30px; top: 150px; text-align: right;
    color: var(--text-light); font-size: 14px; line-height: 24px;
  }
  .contact__line { display: flex; align-items: center; justify-content: flex-end; gap: 6px; }
  .contact__icon { width: 11px; height: 11px; fill: var(--brand-blue); }

  .person {
    position: absolute; left: 32px; bottom: 28px; color: var(--text-light);
  }
  .person__name { color: var(--brand-blue); font-weight: 700; font-size: 20px; line-height: 24px; }
  .person__degree { font-size: 13px; font-weight: 400; }
  .person__role { font-size: 14px; line-height: 20px; }
  .person__address {
    margin-top: 10px; font-size: 14px; line-height: 20px;
    color: var(--text-muted); font-style: normal;
  }
</style>
</head>
<body>
  <main class="sheet">
    <section class="card card--front" aria-label="Business card front">
      <div class="brand">
        <div class="brand__row">
          <span class="brand__dot"></span>
          <span class="brand__name">Amberfield Court</span>
        </div>
        <span class="brand__tagline">Comfort, Respect, Companionship</span>
      </div>

      <div class="contact">
        <div class="contact__line">0472 639 208
          <svg class="contact__icon" viewBox="0 0 24 24" aria-hidden="true"><path d="M6.6 10.8a15.1 15.1 0 0 0 6.6 6.6l2.2-2.2c.3-.3.7-.4 1-.2 1.1.4 2.3.6 3.6.6.6 0 1 .4 1 1V20c0 .6-.4 1-1 1A17 17 0 0 1 3 4c0-.6.4-1 1-1h3.5c.6 0 1 .4 1 1 0 1.3.2 2.5.6 3.6.1.3 0 .7-.2 1z"/></svg>
        </div>
        <div class="contact__line">dwalsh@amberfieldcourt.com.au
          <svg class="contact__icon" viewBox="0 0 24 24" aria-hidden="true"><path d="M2 5h20v14H2z M4 7v1l8 5 8-5V7l-8 5z"/></svg>
        </div>
      </div>

      <div class="person">
        <div class="person__name">Darren Walsh, <span class="person__degree">BCom</span></div>
        <div class="person__role">Finance Manager</div>
        <address class="person__address">
          37 Marrabel Crescent,<br>Brindle Vale, Qld 4093
        </address>
      </div>
    </section>

    <section class="card card--back" aria-label="Business card back">
      <div class="brand">
        <div class="brand__row">
          <span class="brand__dot"></span>
          <span class="brand__name">Amberfield Court</span>
        </div>
        <span class="brand__tagline">Comfort, Respect, Companionship</span>
      </div>
    </section>
  </main>
</body>
</html>
```